I need a SEO-friendly Wordpress website (making sure to style H1, H2, H3, etc correctly) for a Hawaii-based law firm called Meridian Crest Legal Group. Comparable websites include https://brvlaw.example/ and https://www.lomrit.example/ for design reference. The current copy on the TarnAdvocate.example website can be used.

```html
<!DOCTYPE html>
<html lang="en">
<head>
<meta charset="utf-8">
<title>Meridian Crest Legal Group</title>
<link href="https://fonts.googleapis.com/css2?family=Tinos:wght@400;700&family=Mulish:wght@400;600&family=Oswald:wght@500&display=swap" rel="stylesheet">
<style>
:root{
  --brown:#7f2d03;
  --orange:#b35f0c;
  --orange-light:#c2700f;
  --ink:#111;
  --text:#555;
  --grey:#efefef;
  --white:#fff;
}
*{box-sizing:border-box;margin:0;padding:0}
html,body{width:1200px;height:2958px;overflow:hidden}
body{position:relative;background:var(--white);font-family:"Mulish",sans-serif;color:var(--text)}
.abs{position:absolute}
h1,h2,h3,h4{font-family:"Tinos",serif;color:var(--ink)}

/* header */
.site-header{left:0;top:0;width:1200px;height:94px}
.brand{left:76px;top:24px;font-family:"Tinos",serif;font-weight:700;font-size:36px;color:var(--ink)}
.header-call{left:896px;top:22px;display:flex;gap:12px;align-items:center}
.header-call small{display:block;font-size:14px;color:var(--orange);font-weight:600;letter-spacing:.5px}
.header-call strong{display:block;font-family:"Tinos",serif;font-size:25px;color:var(--brown);font-weight:700;line-height:1.1}

/* nav */
.main-nav{left:0;top:94px;width:1200px;height:62px;background:linear-gradient(#b86410,#a2520a 60%,#8f4507)}
.main-nav a{position:absolute;top:0;height:62px;line-height:62px;color:var(--white);text-decoration:none;font-size:15px;letter-spacing:.3px}
.main-nav .active{left:77px;width:125px;text-align:center;background:var(--brown)}
.search{left:789px;top:9px;width:333px;height:45px;border:1px solid rgba(255,255,255,.55);border-radius:3px;color:var(--white);font-size:14px;padding:13px 18px}
.search svg{position:absolute;right:12px;top:12px}

/* hero */
.hero{left:0;top:156px;width:1200px;height:521px;background:linear-gradient(100deg,#d9a46a 0%,#8a6a4e 25%,#4d5a66 50%,#3a4756 75%,#2d3745 100%)}
.hero-copy{right:77px;top:124px;text-align:right;color:var(--white)}
.hero-copy p{font-size:20px}
.hero-copy h1{font-family:"Oswald",sans-serif;font-weight:500;font-size:53px;line-height:62px;color:var(--white);margin-top:6px}
.btn{display:inline-block;background:var(--orange);color:var(--white);font-family:"Tinos",serif;font-weight:700;font-size:19px;letter-spacing:.8px;border-radius:5px;text-align:center}
.hero-btn{margin-top:14px;width:296px;height:55px;line-height:55px;background:#a2410b}
.slide-arrow{top:222px;width:50px;height:50px;border:1.5px solid rgba(255,255,255,.7);border-radius:50%}

/* quick contact */
.quick{top:641px;height:73px;display:flex;align-items:center;border:2px solid var(--white);color:var(--white);box-shadow:0 3px 8px rgba(0,0,0,.2);overflow:hidden}
.quick .ico{width:63px;height:100%;display:flex;align-items:center;justify-content:center;background:rgba(0,0,0,.12);flex:none}
.quick small{display:block;font-size:13px}
.quick b{display:block;font-weight:400;font-size:19px;white-space:nowrap}
.quick .txt{padding-left:33px}
.quick.mail .txt{padding-left:24px}
.quick.mail b{font-size:17px}

/* welcome */
.welcome{left:0;top:770px;width:1200px;text-align:center}
.welcome h2{font-size:41px;line-height:47px;font-weight:700}
.tagline{color:var(--orange);font-size:16px;font-weight:600;margin-top:14px}
.welcome p.body{width:545px;margin:26px auto 0;font-size:14px;line-height:27px;color:#666}
.welcome p.body+p.body{margin-top:14px}
.learn{margin-top:30px;width:187px;height:56px;line-height:56px;background:var(--brown)}

/* practice */
.practice-top{left:0;top:1281px;width:1200px;height:313px;background:var(--brown)}
.practice-bottom{left:0;top:1594px;width:1200px;height:346px;background:var(--grey)}
.practice-head{left:0;top:1336px;width:1200px;text-align:center}
.practice-head h2{color:var(--white);font-size:42px;font-weight:700}
.practice-head p{color:var(--white);font-size:15px;margin-top:12px}
.card{top:1464px;width:250px;height:411px;background:var(--white);text-align:center}
.card .photo{height:209px}
.card h3{font-weight:400;font-size:24px;margin-top:28px}
.card p{font-size:13.5px;line-height:26px;color:#666;padding:0 10px;margin-top:14px}
.card svg.arrow{margin-top:10px}

/* contact form */
.touch{left:0;top:1996px;width:1200px;text-align:center}
.touch h2{font-size:43px;font-weight:700}
.touch .tagline{margin-top:10px}
.field{left:365px;width:468px;background:var(--grey);font-size:13px;color:#333;padding:16px 18px}
.field.first{background:var(--white);border:1px solid var(--orange);color:var(--orange)}
.submit{left:522px;top:2407px;width:155px;height:57px;line-height:57px;background:var(--brown)}

/* footer */
.footer-brand{left:116px;top:2654px}
.footer-brand h2{font-size:36px;font-weight:700}
.footer-brand p{font-size:14.5px;line-height:28px;color:#555;margin-top:12px;width:380px}
.footer-panel{left:600px;top:2530px;width:600px;height:364px;background:var(--orange)}
.info{left:80px;display:flex;gap:20px;color:var(--white)}
.info .dot{width:53px;height:53px;border-radius:50%;background:var(--brown);display:flex;align-items:center;justify-content:center;flex:none}
.info h4{color:var(--white);font-size:21px;font-weight:700}
.info p{font-size:14px;line-height:26px}
.copyright{left:0;top:2894px;width:1200px;height:64px;line-height:64px;background:var(--brown);color:#f1dcc9;font-size:13.5px;text-align:center}
</style>
</head>
<body>

<header class="site-header abs">
  <div class="brand abs">Meridian Crest Legal Group</div>
  <div class="header-call abs">
    <svg width="42" height="42" viewBox="0 0 24 24"><path fill="#7f2d03" d="M6.6 10.8a15.1 15.1 0 0 0 6.6 6.6l2.2-2.2c.3-.3.7-.4 1-.2 1.1.4 2.3.6 3.6.6.6 0 1 .4 1 1V20c0 .6-.4 1-1 1A17 17 0 0 1 3 4c0-.6.4-1 1-1h3.5c.6 0 1 .4 1 1 0 1.3.2 2.5.6 3.6.1.3 0 .7-.2 1z"/></svg>
    <div><small>Call Us Today :</small><strong>+1.808.555.0142</strong></div>
  </div>
</header>

<nav class="main-nav abs">
  <a class="active">HOME</a>
  <a style="left:237px">PRACTIE AREAS</a>
  <a style="left:397px">ATTORNEY</a>
  <a style="left:522px">BLOG</a>
  <a style="left:604px">CONTACT US</a>
  <div class="search abs">Search...
    <svg width="20" height="20" viewBox="0 0 20 20"><circle cx="8" cy="8" r="5.5" fill="none" stroke="#fff" stroke-width="1.8"/><path d="M12 12l6 6" stroke="#fff" stroke-width="2.2"/></svg>
  </div>
</nav>

<section class="hero abs" role="img" aria-label="Photo of a thoughtful lawyer holding a pen and a notebook in a sunlit office">
  <div class="slide-arrow abs" style="left:12px"><svg width="50" height="50" viewBox="0 0 50 50"><path d="M28 16l-9 9 9 9" fill="none" stroke="#fff" stroke-width="1.5"/></svg></div>
  <div class="slide-arrow abs" style="left:1138px"><svg width="50" height="50" viewBox="0 0 50 50"><path d="M22 16l9 9-9 9" fill="none" stroke="#fff" stroke-width="1.5"/></svg></div>
  <div class="hero-copy abs">
    <p>Over 70 years of combined practice, specializing in:</p>
    <h1>Personal Injury Family &amp;<br>Divorce Child Custody</h1>
    <a class="btn hero-btn">GET FREE CONSULTATION</a>
  </div>
</section>

<div class="quick abs" style="left:230px;width:370px;background:var(--brown)">
  <div class="ico"><svg width="28" height="28" viewBox="0 0 24 24"><path fill="#fff" d="M6.6 10.8a15.1 15.1 0 0 0 6.6 6.6l2.2-2.2c.3-.3.7-.4 1-.2 1.1.4 2.3.6 3.6.6.6 0 1 .4 1 1V20c0 .6-.4 1-1 1A17 17 0 0 1 3 4c0-.6.4-1 1-1h3.5c.6 0 1 .4 1 1 0 1.3.2 2.5.6 3.6.1.3 0 .7-.2 1z"/></svg></div>
  <div class="txt"><small>Call Us :</small><b>+1.808.555.0142</b></div>
</div>
<div class="quick mail abs" style="left:600px;width:370px;background:var(--orange)">
  <div class="ico"><svg width="28" height="22" viewBox="0 0 28 22"><rect width="28" height="22" rx="2" fill="#fff"/><path d="M1 2l13 10 13-10" fill="none" stroke="#b35f0c" stroke-width="2"/></svg></div>
  <div class="txt"><small>Email Us :</small><b>clients@tarnadvocate.example</b></div>
</div>

<section class="welcome abs">
  <h2>Welcome To<br>The Kona Lawyers Of MCLG</h2>
  <p class="tagline">Lawyers Serving the Big Island and Neighboring Islands</p>
  <p class="body">The experienced attorneys in the Meridian Crest Legal Group's Kailua Kona, Hawaii office provide clients with a wide range of litigation expertise, including legal claims involving divorce &amp; family, personal injury, toxic exposures, intellectual property, and real estate.</p>
  <p class="body">Our Kona office also offers commercial and hospitality litigation expertise on behalf of a wide variety of clients, including restaurants, hotels, property owners, and many others.</p>
  <a class="btn learn">LEARN MORE</a>
</section>

<div class="practice-top abs"></div>
<div class="practice-bottom abs"></div>
<div class="practice-head abs">
  <h2>Our Practice Areas</h2>
  <p>Dedicated to making sure you receive the care and attention you need.</p>
</div>

<article class="card abs" style="left:77px">
  <div class="photo" role="img" aria-label="Photo of a mother hugging her young child" style="background:linear-gradient(135deg,#8d8a93,#b9a37a 55%,#7c7a82)"></div>
  <h3>Family &amp; Divorce</h3>
  <p>Our lawyers handle all aspects of family law on the Big Island and neighboring islands.</p>
  <svg class="arrow" width="36" height="14" viewBox="0 0 36 14"><path d="M0 7h30M24 1l7 6-7 6" fill="none" stroke="#b35f0c" stroke-width="3"/></svg>
</article>
<article class="card abs" style="left:343px">
  <div class="photo" role="img" aria-label="Photo of an injured man in a neck brace sitting in a waiting room" style="background:linear-gradient(135deg,#d8d6d2,#8e8c88 55%,#3e3b38)"></div>
  <h3>Personal Injury</h3>
  <p>Dealing with personal injury and wrongful death claims is hard enough, so the lawyers .</p>
  <svg class="arrow" width="36" height="14" viewBox="0 0 36 14"><path d="M0 7h30M24 1l7 6-7 6" fill="none" stroke="#b35f0c" stroke-width="3"/></svg>
</article>
<article class="card abs" style="left:609px">
  <div class="photo" role="img" aria-label="Photo of a hand signing a document with a pen" style="background:linear-gradient(135deg,#6a5a4c,#b7b4ae 50%,#e4e2de)"></div>
  <h3>Corporate &amp; IP</h3>
  <p>The attorneys at MCLG have been helping Big Island business owners with all their legal.</p>
  <svg class="arrow" width="36" height="14" viewBox="0 0 36 14"><path d="M0 7h30M24 1l7 6-7 6" fill="none" stroke="#b35f0c" stroke-width="3"/></svg>
</article>
<article class="card abs" style="left:874px">
  <div class="photo" role="img" aria-label="Photo of a businessman pointing at a small model house" style="background:linear-gradient(135deg,#1e1e22,#3a3a40 50%,#c9b6a0)"></div>
  <h3>Real Estate</h3>
  <p>Our lawyers work with home owners, buyers and property developers to ensure timely.</p>
  <svg class="arrow" width="36" height="14" viewBox="0 0 36 14"><path d="M0 7h30M24 1l7 6-7 6" fill="none" stroke="#b35f0c" stroke-width="3"/></svg>
</article>

<section class="touch abs">
  <h2>Keep In Touch</h2>
  <p class="tagline">If you need an have any Qusetion for contact us Today !</p>
</section>
<div class="field first abs" style="top:2103px;height:52px">Name *</div>
<div class="field abs" style="top:2165px;height:52px">Email *</div>
<div class="field abs" style="top:2227px;height:52px">Subject *
  <svg class="abs" style="right:14px;top:23px" width="12" height="7" viewBox="0 0 12 7"><path d="M0 0h12L6 7z" fill="#333"/></svg>
</div>
<div class="field abs" style="top:2290px;height:104px">Message *</div>
<a class="btn submit abs">SUBMIT</a>

<footer>
  <div class="footer-brand abs">
    <h2>Meridian Crest Legal Group</h2>
    <p>Dedicated to making sure you receive the care and attention you need.</p>
  </div>
  <div class="footer-panel abs">
    <div class="info abs" style="top:60px">
      <div class="dot"><svg width="18" height="24" viewBox="0 0 18 24"><path d="M9 0a9 9 0 0 0-9 9c0 7 9 15 9 15s9-8 9-15a9 9 0 0 0-9-9z" fill="#fff"/><circle cx="9" cy="9" r="3.5" fill="#7f2d03"/></svg></div>
      <div><h4>Meridian Crest Legal Group</h4><p style="margin-top:8px">48-2210 Palani Lane, Suite 310<br>Kailua Kona, Hawaii 96745.</p></div>
    </div>
    <div class="info abs" style="top:170px">
      <div class="dot"><svg width="22" height="22" viewBox="0 0 24 24"><path fill="#fff" d="M6.6 10.8a15.1 15.1 0 0 0 6.6 6.6l2.2-2.2c.3-.3.7-.4 1-.2 1.1.4 2.3.6 3.6.6.6 0 1 .4 1 1V20c0 .6-.4 1-1 1A17 17 0 0 1 3 4c0-.6.4-1 1-1h3.5c.6 0 1 .4 1 1 0 1.3.2 2.5.6 3.6.1.3 0 .7-.2 1z"/></svg></div>
      <div><h4>Call Us :</h4><p>+1.808.555.0142</p></div>
    </div>
    <div class="info abs" style="top:255px">
      <div class="dot"><svg width="22" height="17" viewBox="0 0 28 22"><rect width="28" height="22" rx="2" fill="#fff"/><path d="M1 2l13 10 13-10" fill="none" stroke="#7f2d03" stroke-width="2"/></svg></div>
      <div><h4>Email Us :</h4><p>clients@tarnadvocate.example</p></div>
    </div>
  </div>
  <div class="copyright abs">©2019 Meridian Crest Legal Group. - All Rights Reserved. Privacy Policy &nbsp;| Tearms &amp; Condition</div>
</footer>

</body>
</html>
```